Business card design needed

I would like a one sided black business card with the information provided above. Refer to my website www.brightvolleyracquets.com.au for an example of colors I have used for my site, would like to keep this consistent for my business cards also, I will upload my logo below.

I am a new small business that provides tennis customers with racquet re stringing, tennis strings and accessories.

Industry/Entity Type

Small Business

Contact Information for Business Card

Bright Volley Tennis

Owen Whitby
Managing Director

brightvolleyracquets@mailbox.example
www.brightvolleyracquets.com.au
0491 726 305

Racquet Restringing/Tennis Strings/Accessories

Requirements
Must have
• Must have my logo and card must be black

```html
<!DOCTYPE html>
<html lang="en">
<head>
<meta charset="utf-8">
<title>Bright Volley Tennis – Business Card</title>
<link href="https://fonts.googleapis.com/css2?family=Lato:wght@300;400;700;900&display=swap" rel="stylesheet">
<style>
  :root {
    --backdrop: #e4e1dd;
    --card-black: #000000;
    --brand-green: #c4dc2c;
    --brand-blue: #254e88;
    --text-white: #ffffff;
    --title-green: #b9d032;
  }
  * { box-sizing: border-box; margin: 0; padding: 0; }
  html, body {
    width: 1200px;
    height: 475px;
    overflow: hidden;
  }
  body {
    background: var(--backdrop);
    font-family: "Lato", Arial, sans-serif;
    position: relative;
  }
  .card {
    position: absolute;
    width: 546px;
    height: 312px;
    background: var(--card-black);
    border-radius: 14px;
    overflow: hidden;
  }
  .card--front { left: 40px; top: 81px; }
  .card--back { left: 607px; top: 85px; }

  .brand {
    position: absolute;
    left: 0;
    right: 0;
    display: flex;
    align-items: center;
    justify-content: center;
    gap: 12px;
  }
  .brand__dot {
    width: 30px;
    height: 30px;
    border-radius: 50%;
    background: var(--brand-green);
  }
  .brand__name {
    color: var(--brand-green);
    font-weight: 900;
    font-size: 31px;
    letter-spacing: 1px;
    text-transform: uppercase;
  }
  .card--front .brand { top: 86px; }
  .card--back .brand { top: 120px; }

  .wave {
    position: absolute;
    left: 0;
    top: 0;
    width: 100%;
    height: 100%;
  }

  .holder {
    position: absolute;
    left: 60px;
    top: 232px;
    width: 170px;
    text-align: center;
  }
  .holder__name {
    color: var(--title-green);
    font-size: 19px;
    font-weight: 400;
    letter-spacing: 0.5px;
    text-transform: uppercase;
  }
  .holder__role {
    color: var(--title-green);
    font-size: 14px;
    font-weight: 400;
    margin-top: 3px;
  }

  .contact {
    position: absolute;
    left: 256px;
    top: 226px;
    list-style: none;
  }
  .contact__item {
    display: flex;
    align-items: center;
    gap: 9px;
    color: var(--text-white);
    font-size: 15px;
    font-weight: 400;
    line-height: 19px;
  }
  .contact__icon {
    width: 11px;
    height: 11px;
    flex: none;
  }

  .back-url {
    position: absolute;
    left: 0;
    right: 0;
    top: 236px;
    text-align: center;
    color: var(--text-white);
    font-size: 14px;
    letter-spacing: 2.4px;
  }
</style>
</head>
<body>

  <section class="card card--front" aria-label="Business card front">
    <svg class="wave" viewBox="0 0 546 312" preserveAspectRatio="none" aria-hidden="true">
      <path d="M0,174 C120,186 250,196 370,194 C450,192 515,189 546,190 L546,312 L0,312 Z" fill="var(--brand-green)"/>
      <path d="M0,188 C130,196 260,203 380,199 C460,196 520,195 546,196 L546,312 L0,312 Z" fill="var(--card-black)"/>
      <path d="M0,194 C130,200 260,206 380,203 C460,201 520,200 546,201 L546,312 L0,312 Z" fill="var(--brand-blue)"/>
    </svg>

    <div class="brand">
      <span class="brand__dot"></span>
      <span class="brand__name">Bright Volley Tennis</span>
    </div>

    <div class="holder">
      <p class="holder__name">Owen Whitby</p>
      <p class="holder__role">Managing Director</p>
    </div>

    <ul class="contact">
      <li class="contact__item">
        <svg class="contact__icon" viewBox="0 0 12 12" aria-hidden="true">
          <path d="M3,1 L5,3.5 L4,5 C5,7 6,8 7.5,8.5 L9,7.5 L11,9.5 L9.5,11 C5,10.5 1.5,7 1,2.5 Z" fill="var(--title-green)"/>
        </svg>
        <span>0491 726 305</span>
      </li>
      <li class="contact__item">
        <svg class="contact__icon" viewBox="0 0 12 12" aria-hidden="true">
          <rect x="1" y="3" width="10" height="7" fill="var(--title-green)"/>
          <path d="M1,3 L6,7 L11,3" fill="none" stroke="var(--brand-blue)" stroke-width="1"/>
        </svg>
        <span>brightvolleyracquets@mailbox.example</span>
      </li>
      <li class="contact__item">
        <svg class="contact__icon" viewBox="0 0 12 12" aria-hidden="true">
          <circle cx="6" cy="6" r="5" fill="none" stroke="var(--title-green)" stroke-width="1.2"/>
          <path d="M1,6 H11 M6,1 C3,4 3,8 6,11 M6,1 C9,4 9,8 6,11" fill="none" stroke="var(--title-green)" stroke-width="1"/>
        </svg>
        <span>www.brightvolleyracquets.com.au</span>
      </li>
    </ul>
  </section>

  <section class="card card--back" aria-label="Business card back">
    <div class="brand">
      <span class="brand__dot"></span>
      <span class="brand__name">Bright Volley Tennis</span>
    </div>
    <p class="back-url">www.brightvolleyracquets.com.au</p>
  </section>

</body>
</html>
```